K & R Acre Works. Business card design

We need a business card designed for a new business. We have a bulldozer and tractor service. We clear land and make wildlife food plots. We provide disking, bush hogging, and site prep services.
I have attached an image of a business card that I like and would like my business cards to look similar.

Target Market(s)

anyone needing bulldozer and/or tractor services

Industry/Entity Type

Business

Contact Information for Business Card

K & R Acre Works, Operated by 7-T-Ranch
Wade Colton
601-472-3358
wcr4817@fieldmail-example.com

Font styles to use
Sans Serif

Colors

Designer to choose colors to be used in the design.

Requirements
Must have
• image of tractor and bulldozer
• Land Clearing
• Wildlife food plots
• Bush Hogging
• Disking
• Site prep
Nice to have
• i have included a image of a business card that i like. I would like mine to be similar.

```html
<!DOCTYPE html>
<html lang="en">
<head>
<meta charset="utf-8">
<title>K &amp; R Acre Works – Business Card</title>
<link href="https://fonts.googleapis.com/css2?family=Roboto+Condensed:wght@400;700&family=Roboto:wght@400;500&display=swap" rel="stylesheet">
<style>
  :root {
    --page-bg: #e9e7e3;
    --card-bg: #f4f4f3;
    --olive: #958f31;
    --olive-dark: #7d7828;
    --brand-brown: #6b4a1c;
    --ink: #2b2b2b;
    --white: #ffffff;
    --photo-frame: #6a3d1e;
  }
  * { margin: 0; padding: 0; box-sizing: border-box; }
  html, body { width: 1200px; height: 771px; overflow: hidden; }
  body { background: var(--page-bg); position: relative; }

  .card {
    position: absolute;
    left: 120px; top: 111px;
    width: 600px; height: 343px;
    transform: scale(1.6);
    transform-origin: 0 0;
    background: var(--card-bg);
    border-radius: 14px;
    overflow: hidden;
    box-shadow: 0 2px 6px rgba(0,0,0,.18);
    font-family: "Roboto", Arial, sans-serif;
  }

  .brand { position: absolute; left: 36px; top: 110px; }
  .brand-name {
    font-family: "Roboto Condensed", Arial, sans-serif;
    font-weight: 700; font-size: 25px; line-height: 25px;
    color: var(--brand-brown); letter-spacing: .2px;
  }
  .brand-tagline {
    font-family: "Roboto Condensed", Arial, sans-serif;
    font-weight: 700; font-size: 10.6px; color: var(--ink);
    margin-top: 2px; letter-spacing: .1px;
  }

  .photo {
    position: absolute; top: 155px; height: 88px;
    border: 2px solid var(--photo-frame);
  }
  .photo-dozer {
    left: 34px; width: 148px;
    background: linear-gradient(180deg, #5f7a3e 0%, #8a8a56 45%, #7b6a4e 70%, #5e5040 100%);
  }
  .photo-tractor {
    left: 189px; width: 118px;
    background: linear-gradient(180deg, #6f8a40 0%, #8f8a4c 45%, #b55a2c 62%, #8c7a48 100%);
  }

  .panel-shape { position: absolute; left: 0; top: 0; }

  .panel-badge {
    position: absolute; left: 330px; top: 144px;
    width: 54px; height: 54px; border-radius: 50%;
    background: var(--white);
    border: 3px solid #9a9a9a;
    box-shadow: 0 0 0 1px #d8d8d8;
  }

  .contact { position: absolute; left: 410px; top: 68px; color: var(--white); }
  .contact-name {
    font-family: "Roboto Condensed", Arial, sans-serif;
    font-weight: 700; font-size: 21px; line-height: 22px; letter-spacing: .2px;
  }
  .contact-role {
    font-family: "Roboto Condensed", Arial, sans-serif;
    font-size: 14.5px; line-height: 17px; margin-top: 1px;
  }
  .contact-list { list-style: none; margin-top: 14px; }
  .contact-list li {
    display: flex; align-items: center; gap: 6px;
    font-size: 13.5px; line-height: 18px;
  }
  .contact-list svg { width: 12px; height: 12px; flex: none; fill: var(--white); }

  .services-title {
    font-family: "Roboto Condensed", Arial, sans-serif;
    font-weight: 700; font-size: 16.5px; line-height: 18px; margin-top: 13px;
  }
  .services-list { list-style: none; margin-top: 2px; }
  .services-list li { font-size: 14px; line-height: 18px; }
  .services-list li::before { content: "•"; margin-right: 6px; }
  .services-list .inline-sep { margin: 0 3px; }
</style>
</head>
<body>
  <div class="card">
    <div class="brand">
      <div class="brand-name">K &amp; R ACRE WORKS</div>
      <div class="brand-tagline">FOR ALL OF YOUR LAND IMPROVEMENT NEEDS</div>
    </div>

    <div class="photo photo-dozer" role="img" aria-label="Photo of a yellow bulldozer pushing soil on a cleared site"></div>
    <div class="photo photo-tractor" role="img" aria-label="Photo of an orange tractor with front loader in a grassy field"></div>

    <svg class="panel-shape" width="600" height="343" viewBox="0 0 600 343" aria-hidden="true">
      <defs>
        <linearGradient id="panelRim" x1="0" y1="0" x2="0" y2="1">
          <stop offset="0" stop-color="#c9c9c9"/>
          <stop offset=".5" stop-color="#6e6e6e"/>
          <stop offset="1" stop-color="#cfcfcf"/>
        </linearGradient>
      </defs>
      <path d="M600 22 H426 A76 76 0 0 0 350 98 V245 A76 76 0 0 0 426 321 H600 Z" fill="url(#panelRim)"/>
      <path d="M600 28 H428 A72 72 0 0 0 356 100 V243 A72 72 0 0 0 428 315 H600 Z" fill="var(--olive)"/>
    </svg>

    <div class="panel-badge"></div>

    <div class="contact">
      <div class="contact-name">WADE COLTON</div>
      <div class="contact-role">OWNER</div>
      <ul class="contact-list">
        <li><svg viewBox="0 0 24 24"><path d="M6.6 10.8a15 15 0 0 0 6.6 6.6l2.2-2.2a1 1 0 0 1 1-.25 11.4 11.4 0 0 0 3.6.57 1 1 0 0 1 1 1V20a1 1 0 0 1-1 1A17 17 0 0 1 3 4a1 1 0 0 1 1-1h3.5a1 1 0 0 1 1 1c0 1.25.2 2.45.57 3.57a1 1 0 0 1-.25 1z"/></svg>601-472-3358</li>
        <li><svg viewBox="0 0 24 24"><path d="M2 5h20v14H2z M3 6l9 7 9-7" fill="none" stroke="#fff" stroke-width="2"/></svg>wcr4817@fieldmail-example.com</li>
        <li><svg viewBox="0 0 24 24"><circle cx="12" cy="12" r="9" fill="none" stroke="#fff" stroke-width="2"/><path d="M3 12h18M12 3c3 3 3 15 0 18M12 3c-3 3-3 15 0 18" fill="none" stroke="#fff" stroke-width="1.6"/></svg>acreworks-example.com</li>
      </ul>
      <div class="services-title">WE CREADED</div>
      <ul class="services-list">
        <li>Land Clearing</li>
        <li>Wildlife food plots</li>
        <li>Bush Hogging</li>
        <li>Disking<span class="inline-sep">•</span>Site prep</li>
      </ul>
    </div>
  </div>
</body>
</html>
```